Property Finance Company - Orbin Funding Limited

Background: Orbin Funding Group Limited is a private property finance company. Orbin Funding Group has capital to directly fund first mortgage, mezzanine and preferred equity financing. We also acquire performing, sub-performing and distressed debt.

Orbin Fundings management philosophy emphasises expertise, innovation, wisdom, honesty and competitiveness. Orbin Funding are not finance brokers - we provide debt funding to the commercial property and residential development sectors. Our process is built from experience and cumutavely Orbin Fundings Directors have in excess of 60 years wisdom.

The aim of the website will be to increase brand awareness, provide clients with comfort around our level of skill and background on who we are, generate more sales, and provide examples of projects that we have funded.

The website is a new product launch, and we need to use our Orbin Funding logo that has just been designed. We like a dark background, and either black/silver/grey/ jade green, or black/gold/jade green colours.

Our unique advantages are that we have fast turnaround times, we can solve clients funding problems and we know what we are doing. Our target audience will be viewing the website on both desktop and mobile devices.

We would like to have the following pages:

Home
About
Team
Services
Project Experience
Contact

Competitors Website: http://www.tarvolo.example/

We would also like to have the option of video footage in our website, as you can see in our competitors website.

Overall we want a really slick, elegant but modern website that is better than www.tarvolo.example

Target Market(s)

Finance borrowers, property developers, accountants, lawyers, businesspeople, high net worth people

Industry/Entity Type

Finance

Requirements
Must have
• Please see project description
Nice to have
Should not have

```html
<!DOCTYPE html>
<html lang="en">
<head>
<meta charset="utf-8">
<title>Orbin Funding Group</title>
<link rel="stylesheet" href="https://fonts.googleapis.com/css2?family=Cinzel:wght@400;700&family=Mulish:wght@400;600;700&display=swap">
<style>
:root{
  --green:#3c9b3c;
  --green-dark:#2f7f2f;
  --ink:#222;
  --text:#666;
  --dark:#2b2b2b;
  --darker:#1a1a1a;
  --grey:#c9c9c9;
  --light:#f4f4f4;
  --white:#fff;
}
*{box-sizing:border-box;margin:0;padding:0}
html,body{width:1200px;height:4905px;overflow:hidden}
body{font-family:"Mulish",sans-serif;color:var(--text);background:var(--white);position:relative}
.serif{font-family:"Cinzel",serif}
section,header,footer{position:absolute;left:0;width:1200px}
.section-title{font-family:"Cinzel",serif;font-size:36px;color:var(--ink);text-align:center;display:flex;align-items:center;justify-content:center;gap:14px}
.section-title .dot{width:30px;height:30px;border-radius:50%;background:var(--green)}
.on-dark .section-title{color:var(--white)}
.on-dark .section-title .dot{background:var(--white)}
p.copy{font-size:14px;line-height:1.8}

/* hero */
.hero{top:0;height:648px;background:linear-gradient(180deg,#3a3a3a 0%,#5b5650 45%,#2d2b28 100%)}
.hero .photo{position:absolute;inset:0}
.nav{position:absolute;top:0;left:0;width:1200px;height:115px;background:rgba(0,0,0,.55);display:flex;align-items:center;padding:0 70px}
.brand{display:flex;align-items:center;gap:12px;font-family:"Cinzel",serif;color:var(--white);font-size:20px;font-weight:700}
.brand .mark{width:34px;height:34px;border-radius:50%;background:var(--white)}
.menu{margin-left:auto;display:flex;gap:6px;align-items:center;list-style:none}
.menu li{font-family:"Cinzel",serif;color:var(--white);font-size:19px;padding:10px 14px}
.menu li.active{border:2px solid var(--white)}
.search{width:44px;height:44px;border-radius:50%;background:var(--white);margin-left:14px;display:flex;align-items:center;justify-content:center}
.hero h1{position:absolute;top:255px;width:100%;text-align:center;font-family:"Mulish",sans-serif;font-weight:700;font-size:50px;line-height:1.3;color:var(--white);letter-spacing:1px}
.btn{display:inline-block;background:var(--green);color:var(--white);font-weight:700;font-size:20px;padding:18px 44px;border-radius:32px}
.hero .btn{position:absolute;top:412px;left:525px}

/* values */
.values{top:648px;height:300px;display:flex;justify-content:center;gap:0}
.value{width:262px;height:255px;background:var(--grey);text-align:center;padding:40px 28px 0;position:relative;margin-right:4px}
.value.featured{background:var(--green);height:296px;color:var(--white)}
.value .icon{position:absolute;top:-40px;left:86px;width:90px;height:90px;border-radius:50%;background:var(--darker);border:5px solid var(--white)}
.value.featured .icon{background:var(--green-dark)}
.value h3{font-family:"Cinzel",serif;font-size:21px;color:var(--ink);margin-top:50px}
.value.featured h3{color:var(--white)}
.value p{font-size:14px;line-height:1.6;margin-top:10px;color:#555}
.value.featured p{color:var(--white)}
.value .more{position:absolute;left:28px;top:222px;font-size:14px;font-weight:700;color:var(--ink)}
.value.featured .more{color:var(--white)}

/* about */
.about{top:1024px;height:676px;background:var(--dark)}
.about .section-title{padding-top:70px}
.about .video{position:absolute;left:210px;top:155px;width:780px;height:310px;background:linear-gradient(180deg,#d4dfe6,#9aa7ad 70%,#6a5a48)}
.about .play{position:absolute;left:560px;top:282px;width:70px;height:70px;border-radius:50%;background:var(--white)}
.about p.copy{position:absolute;left:125px;top:500px;width:950px;color:#ccc;text-align:center}

/* team */
.team{top:1700px;height:590px;background:var(--white)}
.team .section-title{padding-top:60px}
.team p.copy{width:950px;margin:30px auto 0;text-align:center}
.members{position:absolute;top:240px;left:88px;display:flex;gap:47px}
.member{width:210px;height:210px;border-radius:50%;background:linear-gradient(180deg,#e6e6e6,#a9a9a9);border:7px solid var(--dark);position:relative}
.member.featured{border-color:var(--green)}
.member .name{position:absolute;bottom:12px;left:30px;width:136px;background:var(--white);text-align:center;font-family:"Cinzel",serif;font-size:17px;color:var(--ink);padding:6px 0;line-height:1.1}
.member.featured .name{color:var(--green)}
.dots{position:absolute;top:490px;left:550px;display:flex;gap:10px}
.dots span{width:14px;height:14px;border-radius:50%;background:var(--dark)}
.dots span.on{background:var(--green)}

/* services */
.services{top:2290px;height:572px;background:linear-gradient(180deg,#222 0%,#333 60%,#444 100%)}
.services .section-title{padding-top:50px}
.hub{position:absolute;left:512px;top:232px;width:176px;height:176px;border-radius:50%;background:var(--white);border:10px solid var(--green)}
.hub .core{position:absolute;left:24px;top:24px;width:108px;height:108px;border-radius:50%;background:var(--green)}
.service{position:absolute;width:360px;height:118px;background:var(--green);border-radius:59px;color:var(--white);padding:18px 30px}
.service h4{font-family:"Cinzel",serif;font-size:17px;line-height:1.25}
.service p{font-size:13px;line-height:1.5;margin-top:6px;width:210px}
.service .thumb{position:absolute;top:14px;width:90px;height:90px;border-radius:50%;background:linear-gradient(135deg,#c9c9c9,#8a8a8a);border:4px solid var(--white)}
.service.left{left:78px;padding-left:30px}
.service.left .thumb{right:14px}
.service.right{left:762px;padding-left:140px}
.service.right .thumb{left:14px}
.service.right p{width:200px}

/* blog */
.blog{top:2862px;height:736px;background:var(--white)}
.blog .section-title{padding-top:60px}
.posts{position:absolute;top:138px;left:78px;display:flex;gap:20px}
.post{width:340px;height:518px;border:2px solid #ccc;position:relative}
.post .img{height:218px;background:linear-gradient(180deg,#cfcfcf,#8e8e8e)}
.post .date{position:absolute;left:22px;top:190px;width:70px;height:76px;background:var(--white);border:3px solid var(--green);text-align:center;color:var(--ink)}
.post .date b{display:block;font-size:28px;margin-top:6px}
.post .date small{font-size:11px;font-weight:700}
.post h5{margin:72px 22px 0;font-family:"Cinzel",serif;font-size:19px;color:var(--ink);line-height:1.3}
.post.featured h5{color:var(--green)}
.post p{margin:10px 22px 0;font-size:14px;line-height:1.6}
.post .more{position:absolute;bottom:40px;left:22px;right:22px;display:flex;align-items:center;gap:14px;font-size:14px;font-weight:700;color:var(--green)}
.post .more i{flex:1;height:2px;background:var(--green)}

/* contact */
.contact{top:3598px;height:530px}
.map{position:absolute;left:0;top:0;width:600px;height:530px;background:linear-gradient(135deg,#ecebe6,#dcdccf)}
.map .pin{position:absolute;left:286px;top:192px}
.contact-form{position:absolute;left:600px;top:0;width:600px;height:530px;background:var(--green);color:var(--white);padding:48px 60px}
.contact-form h2{font-family:"Cinzel",serif;font-size:36px;display:flex;align-items:center;gap:14px}
.contact-form h2 .dot{width:30px;height:30px;border-radius:50%;background:var(--white)}
.field{border-bottom:1px solid rgba(255,255,255,.7);height:52px;padding-top:24px;font-size:14px;width:400px}
.field.tall{height:110px}
.contact-form .submit{display:inline-block;margin-top:40px;background:var(--white);color:var(--ink);font-weight:700;font-size:16px;padding:14px 28px}

/* newsletter */
.newsletter{top:4128px;height:245px;background:var(--white)}
.newsletter h2{position:absolute;left:78px;top:60px;font-family:"Cinzel",serif;font-size:36px;color:var(--ink);display:flex;align-items:center;gap:14px}
.newsletter h2 .dot{width:30px;height:30px;border-radius:50%;background:var(--dark)}
.newsletter p{position:absolute;left:78px;top:120px;width:500px;font-size:14px;line-height:1.6}
.subscribe{position:absolute;left:595px;top:112px;display:flex}
.subscribe .input{width:390px;height:62px;border:1px solid #bbb;padding:20px;font-size:14px}
.subscribe .go{background:var(--green);color:var(--white);font-size:18px;height:62px;padding:20px 22px;font-family:"Cinzel",serif;line-height:1}

/* footer */
.footer{top:4373px;height:532px;background:linear-gradient(180deg,#f2f2f2,#c6cbd0)}
.col{position:absolute;top:50px;width:220px}
.col h6{font-family:"Cinzel",serif;font-size:20px;color:var(--green);margin-bottom:16px}
.col li{list-style:none;font-size:14px;line-height:1.9;color:var(--ink)}
.tweet{display:flex;gap:10px;font-size:12px;line-height:1.5;margin-bottom:20px;color:var(--ink)}
.tweet .t{width:22px;height:22px;border-radius:50%;background:var(--green);flex:none}
.footer-brand{position:absolute;left:852px;top:0;width:270px;height:451px;background:var(--green);color:var(--white);padding:60px 30px 0}
.footer-brand .name{display:flex;flex-direction:column;align-items:center;gap:12px;font-family:"Cinzel",serif;font-size:26px;text-align:center}
.footer-brand .name .mark{width:60px;height:60px;border-radius:50%;background:var(--white)}
.footer-brand ul{margin-top:36px;list-style:none}
.footer-brand li{font-size:13px;line-height:1.5;margin-bottom:16px;display:flex;gap:10px}
.footer-brand li i{width:16px;height:16px;border-radius:50%;background:var(--white);flex:none;margin-top:2px}
.bottom{position:absolute;left:0;top:451px;width:1200px;height:81px;background:var(--darker);color:#ccc;font-size:13px;display:flex;align-items:center;padding:0 78px}
.social{margin-left:auto;display:flex;gap:10px}
.social span{width:32px;height:32px;border-radius:50%;border:2px solid var(--white)}
</style>
</head>
<body>

<header class="hero">
  <div class="photo" role="img" aria-label="Photo of a modern loft office interior with large windows"></div>
  <nav class="nav">
    <div class="brand"><span class="mark"></span>Orbin Funding Group</div>
    <ul class="menu">
      <li class="active">Home</li><li>About</li><li>Team</li><li>Services</li><li>Project Experience</li><li>Contact</li>
    </ul>
    <div class="search"><svg width="20" height="20" viewBox="0 0 20 20"><circle cx="8" cy="8" r="6" fill="none" stroke="#222" stroke-width="2"/><line x1="12.5" y1="12.5" x2="18" y2="18" stroke="#222" stroke-width="2"/></svg></div>
  </nav>
  <h1>A WIDE RANGE OF GLOBLE<br>INVESTMENT</h1>
  <span class="btn">CONTACT US</span>
</header>

<section class="values">
  <div class="value"><span class="icon"></span><h3>Innovation</h3><p>Lorem Ipsum is simply dummy text of the printing and typesetting industry.</p><span class="more">READ MORE &rarr;</span></div>
  <div class="value featured"><span class="icon"></span><h3>Wisdom</h3><p>Lorem Ipsum is simply dummy text of the printing and typesetting industry.</p><span class="more">READ MORE &rarr;</span></div>
  <div class="value"><span class="icon"></span><h3>Honesty</h3><p>Lorem Ipsum is simply dummy text of the printing and typesetting industry.</p><span class="more">READ MORE &rarr;</span></div>
  <div class="value"><span class="icon"></span><h3>Competitiveness</h3><p>Lorem Ipsum is simply dummy text of the printing and typesetting industry.</p><span class="more">READ MORE &rarr;</span></div>
</section>

<section class="about on-dark">
  <h2 class="section-title"><span class="dot"></span>About Orbin Funding Group</h2>
  <div class="video" role="img" aria-label="Video still of a businessman lassoing a stack of coins"></div>
  <svg class="play" viewBox="0 0 70 70"><circle cx="35" cy="35" r="33" fill="#fff"/><circle cx="35" cy="35" r="26" fill="#d11"/><polygon points="28,22 50,35 28,48" fill="#fff"/></svg>
  <p class="copy">Lorem Ipsum is simply dummy text of the printing and typesetting industry. Lorem Ipsum has been the industry's standard dummy text ever since the 1500s, when an unknown printer took a galley of type and scrambled it to make a type specimen book. It has survived not only five centuries, but also the leap into electronic typesetting, remaining essentially unchanged.</p>
</section>

<section class="team">
  <h2 class="section-title"><span class="dot"></span>Meet Our Teem</h2>
  <p class="copy">Lorem Ipsum is simply dummy text of the printing and typesetting industry. Lorem Ipsum has been the industry's standard dummy text ever since the 1500s, when an unknown printer took a galley of type and scrambled it to make a type specimen book. It has survived not only five centuries, but also the leap into electronic typesetting, remaining essentially unchanged.</p>
  <div class="members">
    <div class="member" role="img" aria-label="Portrait of team member Marlo Venn"><span class="name">Marlo<br>Venn</span></div>
    <div class="member featured" role="img" aria-label="Portrait of team member Ravi Toller"><span class="name">Ravi<br>Toller</span></div>
    <div class="member" role="img" aria-label="Portrait of team member Ines Carrow"><span class="name">Ines Carrow</span></div>
    <div class="member" role="img" aria-label="Portrait of team member Oscar Delane"><span class="name">Oscar<br>Delane</span></div>
  </div>
  <div class="dots"><span></span><span></span><span class="on"></span><span></span></div>
</section>

<section class="services on-dark">
  <h2 class="section-title"><span class="dot"></span>Our Expertize &amp; Services</h2>
  <svg style="position:absolute;left:0;top:0" width="1200" height="572"><g stroke="#3c9b3c" stroke-width="4"><line x1="438" y1="228" x2="540" y2="270"/><line x1="762" y1="228" x2="660" y2="270"/><line x1="438" y1="430" x2="540" y2="380"/><line x1="762" y1="430" x2="660" y2="380"/></g></svg>
  <div class="service left" style="top:170px"><h4>Debt Funding</h4><p>Lorem Ipsum is simply dummy text of the printing and typesetting industry.</p><span class="thumb" role="img" aria-label="Photo of financial documents"></span></div>
  <div class="service right" style="top:170px"><h4>Mezzanine</h4><p>Lorem Ipsum is simply dummy text of the printing and typesetting industry.</p><span class="thumb" role="img" aria-label="Photo of a building interior"></span></div>
  <div class="service left" style="top:372px"><h4>Equity Financing</h4><p>Lorem Ipsum is simply dummy text of the printing and typesetting industry.</p><span class="thumb" role="img" aria-label="Photo of a handshake"></span></div>
  <div class="service right" style="top:372px;padding-top:10px"><h4>Perdorming, sub-performing and distressed debt</h4><p>Lorem Ipsum is simply and typesetting industry.</p><span class="thumb" role="img" aria-label="Photo of a person at a laptop"></span></div>
  <div class="hub"><span class="core"></span></div>
</section>

<section class="blog">
  <h2 class="section-title"><span class="dot"></span>Recent Blog</h2>
  <div class="posts">
    <article class="post featured"><div class="img" role="img" aria-label="Photo of two businessmen shaking hands"></div><div class="date"><b>18</b><small>DEC</small></div><h5>Lorem Ipsum dummy printing typesetting industry.</h5><p>Lorem Ipsum is simply dummy text of the printing and typesetting industry. Lorem Ipsum has been the industry's standard.</p><span class="more"><i></i>READ MORE</span></article>
    <article class="post"><div class="img" role="img" aria-label="Photo of a team meeting in an office"></div><div class="date"><b>18</b><small>DEC</small></div><h5>Lorem Ipsum dummy printing typesetting industry.</h5><p>Lorem Ipsum is simply dummy text of the printing and typesetting industry. Lorem Ipsum has been the industry's standard.</p><span class="more"><i></i>READ MORE</span></article>
    <article class="post"><div class="img" role="img" aria-label="Photo of a group working at a table with charts"></div><div class="date"><b>18</b><small>DEC</small></div><h5>Lorem Ipsum dummy printing typesetting industry.</h5><p>Lorem Ipsum is simply dummy text of the printing and typesetting industry. Lorem Ipsum has been the industry's standard.</p><span class="more"><i></i>READ MORE</span></article>
  </div>
</section>

<section class="contact">
  <div class="map" role="img" aria-label="Street map showing the office location"></div>
  <svg class="map pin" style="left:286px;top:192px;width:28px;height:40px;background:none" viewBox="0 0 28 40"><path d="M14 0C6 0 0 6 0 14c0 10 14 26 14 26s14-16 14-26C28 6 22 0 14 0z" fill="#d22"/><circle cx="14" cy="14" r="5" fill="#fff"/></svg>
  <div class="contact-form">
    <h2><span class="dot"></span>Contact Us Now</h2>
    <div class="field">Name :</div>
    <div class="field">Phone :</div>
    <div class="field">Email :</div>
    <div class="field tall">Message :</div>
    <span class="submit">SUBMIT</span>
  </div>
</section>

<section class="newsletter">
  <h2><span class="dot"></span>Newsletter</h2>
  <p>Send us an email and we'll get in touch shortly, or phone between 8 : 00 and 18 : 00 Monday to Friday - we would be delighted to speak.</p>
  <div class="subscribe"><div class="input">Email :</div><div class="go">SUBSCRIBE</div></div>
</section>

<footer class="footer">
  <div class="col" style="left:78px"><h6>Usefull Link</h6><ul><li>Home</li><li>About</li><li>Team</li><li>Services</li><li>Project Experiences</li><li>Contact</li></ul></div>
  <div class="col" style="left:308px"><h6>Our Services</h6><ul><li>Debt funding</li><li>Mezzanine</li><li>Equity financing</li><li>Performing, sub-performing and distressed debt</li></ul></div>
  <div class="col" style="left:560px;width:260px"><h6>Twitter Feeds</h6>
    <div class="tweet"><span class="t"></span><span>@orbinfunding - 25 min<br>New funding round open for local property projects this week. Read more on our news page today.</span></div>
    <div class="tweet"><span class="t"></span><span>@orbinfunding - 25 min<br>New funding round open for local property projects this week. Read more on our news page today.</span></div>
  </div>
  <div class="footer-brand">
    <div class="name"><span class="mark"></span>Orbin Funding<br>Group</div>
    <ul><li><i></i>123 Building Name, Street, City, Country - Zip code</li><li><i></i>123.0456.7890</li><li><i></i>info@orbinfunding.example</li></ul>
  </div>
  <div class="bottom"><span>&copy; ORBIN FUNDING GROUP - 2017. All Rights Reserved</span><div class="social"><span></span><span></span><span></span><span></span></div></div>
</footer>

</body>
</html>
```